Website for Swedish wellness company "Heartmeadow"

We need a website for our Swedish wellness company. The name is "Heartmeadow" . The company is all about sustainablility for our body, soul and planet. We work with coaching, yoga, massage, healthy food, retreats(sports, excercise, sufing), healing and inspirational talks. We are convinced that personal sustainability and a strong spiritual connection to yourself will lead to planetary sustainability. Our customers are both companies and consumers from all over the world. The final design should be clean/simple and you should get a feeling of community, happiness, warmth, connection,, joy, spirituality but still a professional touch.Just got a logo from Pixel Harbor and are very happy with it;-)
Updates

Sorry I was too enthusiastic posting this project. Of course I will give you some text as well för the different pages! I will see to that it is finished by friday so if you want to wait with your submissions please do! Best regards Maria

Target Market(s)

Businesses and consumers

Industry/Entity Type

Health And Wellness

Number of Pages Required

5+ page

Font styles to use
Sans Serif

Colors
33a6d7
00a990
b7a5cd

Requirements
Must have
• Idea about pages:
• I am not sure how many pages I get for the price, but 5 would be nice to start with.
• Not sure what write ups is;-)
• But title of the pages could be:
• Landing page
• About us
• Services
• Retreats
• Contact us
Nice to have
• A clean and professional website but with some heart and soul in it. Because we Would love colours that harmonize with our logo, but other ideas are welcome!

```html
<!DOCTYPE html>
<html lang="en">
<head>
<meta charset="utf-8">
<title>Heartmeadow – Swedish wellness company</title>
<link href="https://fonts.googleapis.com/css2?family=Exo+2:wght@300;400;600;700&family=Ubuntu:wght@300;400;500;700&display=swap" rel="stylesheet">
<style>
:root{
  --purple:#a892c4;
  --teal:#1fa08f;
  --blue:#2f97d2;
  --navy:#142a4d;
  --ink:#222;
  --text:#333;
  --field:#ececec;
  --grad:linear-gradient(90deg,#1fa08f 0%,#3e9aa6 55%,#8a8fc4 100%);
}
*{box-sizing:border-box;margin:0;padding:0}
html,body{width:1200px;height:2987px;overflow:hidden}
body{position:relative;background:#fff;font-family:"Ubuntu",sans-serif;color:var(--text)}
.abs{position:absolute}

/* top bar */
.topbar{left:0;top:0;width:1200px;height:31px;background:var(--purple);color:#fff;font-size:13px}
.topbar .welcome{left:75px;top:7px}
.topbar .contacts{right:66px;top:7px;display:flex;gap:52px}
.topbar .contacts span{display:flex;align-items:center;gap:5px}

/* header */
.header{left:0;top:31px;width:1200px;height:101px;background:#fff}
.brand-badge{left:58px;top:80px;width:280px;height:120px;background:#fff;border-radius:0 0 140px 140px / 0 0 80px 80px;z-index:3}
.brand{left:60px;top:40px;width:276px;z-index:4;text-align:center}
.brand .mark{width:58px;height:58px;border-radius:50%;border:4px solid #34b3ad;margin:0 auto 8px}
.brand .name{font-weight:500;font-size:27px;color:var(--navy);letter-spacing:.5px}
.nav{right:66px;top:69px;display:flex;align-items:center;gap:30px;font-size:13px;color:#222;text-transform:uppercase;z-index:4}
.nav .active{background:var(--grad);color:#fff;font-weight:500;padding:9px 20px;border-radius:18px;margin-right:-16px}

/* hero */
.hero{left:0;top:132px;width:1200px;height:600px;overflow:hidden}
.hero .photo{position:absolute;inset:0;background:linear-gradient(180deg,#8d85b8 0%,#c8a3b8 30%,#e6b491 52%,#b48a7a 72%,#5e4a52 100%)}
.hero h1{position:absolute;left:199px;top:160px;font-family:"Exo 2",sans-serif;font-weight:700;font-size:66px;color:#2a2526;letter-spacing:1px}
.btn{display:flex;align-items:center;justify-content:center;background:var(--grad);color:#fff;font-family:"Exo 2",sans-serif;font-weight:600;border-radius:30px}
.hero .btn{position:absolute;left:192px;top:251px;width:188px;height:58px;font-size:20px}
.hero .dots{position:absolute;left:551px;top:507px;display:flex;gap:17px;z-index:2}
.hero .dots i{width:12px;height:12px;border-radius:50%;background:#2f97d2}
.hero .dots i.on{background:#fff}
.hero-wave{left:0;top:600px}

/* welcome */
.welcome-title{left:0;top:772px;width:1200px;text-align:center;font-family:"Exo 2",sans-serif;font-weight:300;font-size:38px;color:#111}
.welcome-title b{font-weight:700}
.welcome-sub{left:0;top:836px;width:1200px;text-align:center;font-size:23px;color:#222}
.welcome-text{left:105px;top:887px;width:990px;text-align:center;font-size:14.5px;line-height:22px;color:#333}

/* features */
.arrow-tab{top:1204px;width:32px;height:49px;background:var(--blue);display:flex;align-items:center;justify-content:center}
.feature{top:1030px;width:320px;text-align:center}
.feature .icon{width:150px;height:150px;margin:0 auto;border-radius:24px;background:linear-gradient(150deg,#cdebea 0%,#e6f5f4 55%,#f4faf9 100%)}
.feature h3{margin-top:20px;font-family:"Exo 2",sans-serif;font-weight:600;font-size:23px;color:#222}
.feature p{margin-top:32px;font-size:13px;line-height:22px;color:#333;padding:0 10px}
.feature .diamond{width:27px;height:27px;margin:22px auto 0;transform:rotate(45deg);background:linear-gradient(135deg,#1fa08f,#5b8fb5);display:flex;align-items:center;justify-content:center}
.feature .diamond svg{transform:rotate(-45deg)}

/* banner */
.banner{left:0;top:1443px;width:1200px;height:640px;overflow:hidden}
.banner .photo{position:absolute;inset:0;background:linear-gradient(120deg,#4e7f9e 0%,#6a9cbd 40%,#5b8fb3 65%,#3d6c91 100%)}
.banner .waves{position:absolute;left:0;top:0}
.banner h2{position:absolute;left:0;top:170px;width:1200px;text-align:center;font-family:"Exo 2",sans-serif;font-weight:700;font-size:35px;color:#fff}
.banner p{position:absolute;left:100px;top:228px;width:1000px;text-align:center;font-size:17px;line-height:28px;color:#fff}
.banner .btn{position:absolute;left:506px;top:351px;width:188px;height:58px;font-size:19px}
.banner .ctrls{position:absolute;left:558px;top:491px;display:flex;gap:11px}
.banner .ctrls span{width:37px;height:37px;border-radius:50%;border:2px solid #fff;display:flex;align-items:center;justify-content:center}

/* contact */
.contact-title{left:0;top:2163px;width:1200px;text-align:center;font-family:"Exo 2",sans-serif;font-weight:300;font-size:38px;color:#111}
.contact-title b{font-weight:700}
.field{background:var(--field);font-size:14px;font-weight:500;color:#222;text-transform:uppercase;padding:13px 21px}
.field.name{left:198px;top:2267px;width:392px;height:47px;padding-top:15px}
.field.email{left:611px;top:2267px;width:392px;height:47px;padding-top:15px}
.field.msg{left:198px;top:2325px;width:805px;height:101px}
.contact-note{left:0;top:2442px;width:1200px;text-align:center;font-size:20px;color:#222;letter-spacing:.3px}
.submit{left:515px;top:2503px;width:170px;height:58px;font-size:17px}

/* footer */
.footer{left:0;top:2588px;width:1200px;height:354px;background:linear-gradient(90deg,#1c9c8e 0%,#2192bb 60%,#2f97d2 100%);color:#fff}
.footer .brand-f{position:absolute;left:0;top:40px;width:1200px;text-align:center}
.footer .brand-f .mark{width:70px;height:70px;border-radius:50%;border:4px solid #fff;margin:0 auto 12px}
.footer .brand-f .name{font-weight:500;font-size:29px;letter-spacing:.5px}
.footer .fnav{position:absolute;left:0;top:195px;width:1200px;display:flex;justify-content:center;gap:31px;font-size:13px;text-transform:uppercase}
.footer .finfo{position:absolute;left:0;top:242px;width:1200px;display:flex;justify-content:center;align-items:center;gap:10px;font-size:13px}
.footer .social{position:absolute;left:0;top:290px;width:1200px;display:flex;justify-content:center;gap:45px}
.footer .social i{width:16px;height:16px;border-radius:3px;background:#fff}
.bottombar{left:0;top:2941px;width:1200px;height:46px;background:var(--purple);color:#fff;font-size:13px}
.bottombar .copy{left:0;top:15px;width:1200px;text-align:center}
.bottombar .ver{right:52px;top:15px}
</style>
</head>
<body>

<div class="abs topbar">
  <div class="abs welcome">Welcome To Heartmeadow</div>
  <div class="abs contacts">
    <span><svg width="12" height="12" viewBox="0 0 24 24"><path fill="#fff" d="M6.6 10.8a15 15 0 006.6 6.6l2.2-2.2a1 1 0 011-.25 11 11 0 003.5.56 1 1 0 011 1V20a1 1 0 01-1 1A17 17 0 013 4a1 1 0 011-1h3.5a1 1 0 011 1 11 11 0 00.56 3.5 1 1 0 01-.25 1z"/></svg> Contact Us &nbsp;: &nbsp;1-800 555 0142</span>
    <span><svg width="13" height="11" viewBox="0 0 24 20"><rect x="1" y="1" width="22" height="18" fill="none" stroke="#fff" stroke-width="2.5"/><path d="M1 2l11 9 11-9" fill="none" stroke="#fff" stroke-width="2.5"/></svg> : hello@heartmeadow.example</span>
  </div>
</div>

<div class="abs header"></div>
<div class="abs brand-badge"></div>
<div class="abs brand">
  <div class="mark"></div>
  <div class="name">HEARTMEADOW</div>
</div>
<nav class="abs nav">
  <span class="active">Home</span>
  <span>About Us</span>
  <span>Services</span>
  <span>Retreats</span>
  <span>Contact Us</span>
</nav>

<section class="abs hero">
  <div class="photo" role="img" aria-label="Woman meditating in a yoga pose on a beach at sunset"></div>
  <h1>HEARTMEADOW</h1>
  <div class="btn">Learn More</div>
  <div class="dots"><i></i><i class="on"></i><i></i><i></i></div>
</section>
<svg class="abs hero-wave" width="1200" height="140" viewBox="0 0 1200 140">
  <path d="M0,14 Q600,190 1200,14 L1200,140 L0,140 Z" fill="#a892c4"/>
  <path d="M0,30 Q600,230 1200,30 L1200,140 L0,140 Z" fill="#fff"/>
</svg>

<h2 class="abs welcome-title">WELCOME TO <b>HEARTMEADOW</b></h2>
<div class="abs welcome-sub">Swedish wellness company</div>
<p class="abs welcome-text">Lorem ipsum dolor sit amet, consectetur adipiscing elit, sed do eiusmod tempor incididunt ut labore et dolore magna aliqua. Ut enim ad minim veniam, quis nostrud exercitation ullamco laboris nisi ut aliquip ex ea commodo consequat. Duis aute irure dolor in reprehenderit in voluptate velit esse cillum dolore eu fugiat nulla pariatur. Excepteur sint occaecat cupidatat non proident, sunt in culpa qui officia deserunt mollit anim id est laborum.</p>

<div class="abs arrow-tab" style="left:0"><svg width="10" height="14" viewBox="0 0 10 14"><path d="M8 1L2 7l6 6" fill="none" stroke="#fff" stroke-width="2.5"/></svg></div>
<div class="abs arrow-tab" style="right:0"><svg width="10" height="14" viewBox="0 0 10 14"><path d="M2 1l6 6-6 6" fill="none" stroke="#fff" stroke-width="2.5"/></svg></div>

<div class="abs feature" style="left:85px">
  <div class="icon" role="img" aria-label="Line illustration of a planet with a star"></div>
  <h3>Soul and planet</h3>
  <p>Sed ut perspiciatis unde omnis iste natus error sit voluptatem accusantium doloremque laudantium, totam rem aperiam, eaque ipsa.</p>
  <div class="diamond"><svg width="10" height="7" viewBox="0 0 10 7"><path d="M1 1l4 4 4-4" fill="none" stroke="#fff" stroke-width="2"/></svg></div>
</div>
<div class="abs feature" style="left:440px">
  <div class="icon" role="img" aria-label="Line illustration of a person in a yoga pose"></div>
  <h3>Yoga</h3>
  <p>Sed ut perspiciatis unde omnis iste natus error sit voluptatem accusantium doloremque laudantium, totam rem aperiam, eaque ipsa.</p>
  <div class="diamond"><svg width="10" height="7" viewBox="0 0 10 7"><path d="M1 1l4 4 4-4" fill="none" stroke="#fff" stroke-width="2"/></svg></div>
</div>
<div class="abs feature" style="left:795px">
  <div class="icon" role="img" aria-label="Line illustration of a massage treatment"></div>
  <h3>Massage</h3>
  <p>Sed ut perspiciatis unde omnis iste natus error sit voluptatem accusantium doloremque laudantium, totam rem aperiam, eaque ipsa.</p>
  <div class="diamond"><svg width="10" height="7" viewBox="0 0 10 7"><path d="M1 1l4 4 4-4" fill="none" stroke="#fff" stroke-width="2"/></svg></div>
</div>

<section class="abs banner">
  <div class="photo" role="img" aria-label="Woman relaxing during a massage with candles in the background"></div>
  <svg class="waves" width="1200" height="640" viewBox="0 0 1200 640">
    <path d="M0,0 L1200,0 L1200,122 Q600,-118 0,122 Z" fill="#fff"/>
    <path d="M0,122 Q600,-118 1200,122 L1200,133 Q600,-71 0,133 Z" fill="#2f97d2"/>
    <path d="M0,516 Q600,690 1200,516 L1200,528 Q600,726 0,528 Z" fill="#2f97d2"/>
    <path d="M0,528 Q600,726 1200,528 L1200,640 L0,640 Z" fill="#fff"/>
  </svg>
  <h2>FINIBUS BONORUM ET MALORUM</h2>
  <p>Sed ut perspiciatis unde omnis iste natus error sit voluptatem accusantium doloremque laudantium, totam rem aperiam, eaque ipsa quae ab illo inventore veritatis et quasi architecto beatae vitae dicta sunt explicabo. Nemo enim ipsam voluptatem quia voluptas sit aspernatur aut odit aut fugit, sed quia consequuntur magni dolores</p>
  <div class="btn">Learn More</div>
  <div class="ctrls">
    <span><svg width="14" height="12" viewBox="0 0 14 12"><path d="M13 6H2M6 1L1 6l5 5" fill="none" stroke="#fff" stroke-width="2"/></svg></span>
    <span><svg width="14" height="12" viewBox="0 0 14 12"><path d="M1 6h11M8 1l5 5-5 5" fill="none" stroke="#fff" stroke-width="2"/></svg></span>
  </div>
</section>

<h2 class="abs contact-title">CONTACT <b>US</b></h2>
<div class="abs field name">Name</div>
<div class="abs field email">Email</div>
<div class="abs field msg">Message</div>
<div class="abs contact-note">Please contact me for an appointment</div>
<div class="abs btn submit">SUBMIT</div>

<footer class="abs footer">
  <div class="brand-f">
    <div class="mark"></div>
    <div class="name">HEARTMEADOW</div>
  </div>
  <div class="fnav"><span>Home</span><span>About Us</span><span>Services</span><span>Retreats</span><span>Contact Us</span></div>
  <div class="finfo">
    <svg width="13" height="13" viewBox="0 0 24 24"><path fill="#fff" d="M6.6 10.8a15 15 0 006.6 6.6l2.2-2.2a1 1 0 011-.25 11 11 0 003.5.56 1 1 0 011 1V20a1 1 0 01-1 1A17 17 0 013 4a1 1 0 011-1h3.5a1 1 0 011 1 11 11 0 00.56 3.5 1 1 0 01-.25 1z"/></svg>
    <span>&nbsp; 1-800 555 0178 &nbsp;</span>
    <svg width="13" height="11" viewBox="0 0 24 20"><rect x="0" y="0" width="24" height="20" fill="#fff"/><path d="M1 2l11 9 11-9" fill="none" stroke="#2192bb" stroke-width="2.5"/></svg>
    <span>&nbsp;info@heartmeadow.example</span>
  </div>
  <div class="social" role="img" aria-label="Social network links"><i></i><i></i><i></i><i></i><i></i><i></i><i></i></div>
</footer>
<div class="abs bottombar">
  <div class="abs copy">© 2019 &nbsp;| &nbsp; www.heartmeadow.example</div>
  <div class="abs ver">M1</div>
</div>

</body>
</html>
```